Brindle Asset Management Vendor Recruiting Email

We need a digital flyer to email and post on Social media to attract new vendors to our website to apply to complete maintenance work on our clients homes. I have one flyer we had produced recently that we are un-happy with. It is attached.

The example given is what we do not want!! We do not want any of the pictures used from the existing one

Target Market(s)

Construction companies and handyman

Industry/Entity Type

Residential maintenance and repairs

Requirements
Must have
• Join our team as the header not become a vendor

```html
<!DOCTYPE html>
<html lang="en">
<head>
<meta charset="utf-8">
<title>Join Our Team – Brindle Asset Management</title>
<link href="https://fonts.googleapis.com/css2?family=Great+Vibes&family=Montserrat:ital,wght@0,500;0,600;0,800;1,700&family=Oswald:wght@600&display=swap" rel="stylesheet">
<style>
  :root {
    --page: #ffffff;
    --charcoal: #3a3a3c;
    --charcoal-deep: #2b2b2e;
    --navy: #1f2c5e;
    --navy-deep: #0f0f22;
    --lime: #d4dd1f;
    --purple: #6a2a93;
    --white: #ffffff;
  }
  * { box-sizing: border-box; margin: 0; padding: 0; }
  html, body {
    width: 1200px; height: 1200px; overflow: hidden;
    background: var(--page);
  }
  .flyer {
    position: absolute; left: 20px; top: 80px;
    width: 1160px; height: 1039px;
    overflow: hidden;
    font-family: "Montserrat", sans-serif;
    color: var(--white);
  }
  .flyer__photo {
    position: absolute; inset: 0;
    background: linear-gradient(90deg, var(--charcoal) 0%, var(--charcoal-deep) 45%, #2a3257 70%, var(--navy) 100%);
  }
  .flyer__frame {
    position: absolute; left: 33px; top: 20px; width: 1096px; height: 998px;
    border: 1.5px solid var(--white); border-radius: 26px;
  }
  .headline { position: absolute; left: 0; right: 0; text-align: center; }
  .headline__script {
    top: 52px;
    font-family: "Great Vibes", cursive;
    font-size: 104px; line-height: 1;
  }
  .headline__main {
    top: 140px;
    font-family: "Montserrat", sans-serif;
    font-weight: 600; font-size: 132px; line-height: 1;
    letter-spacing: 4px;
    color: var(--lime);
  }
  .perks, .requirements__list { list-style: none; position: absolute; }
  .perks li, .requirements__list li {
    position: absolute; left: 0;
    font-weight: 500; line-height: 1.28;
  }
  .perks li::before, .requirements__list li::before {
    content: ""; position: absolute;
    width: 11px; height: 11px; border-radius: 50%;
    background: var(--lime);
  }
  .perks { left: 95px; top: 0; width: 450px; }
  .perks li { font-size: 24px; width: 450px; }
  .perks li::before { left: -27px; top: 10px; }
  .divider {
    position: absolute; left: 562px; top: 298px; width: 2px; height: 440px;
    background: var(--white);
  }
  .requirements__title {
    position: absolute; left: 593px; top: 298px;
    font-family: "Oswald", sans-serif; font-weight: 600;
    font-size: 40px; line-height: 50px; letter-spacing: 0.3px;
  }
  .requirements__list { left: 627px; top: 0; width: 500px; }
  .requirements__list li { font-size: 21px; width: 500px; }
  .requirements__list li::before { left: -27px; top: 9px; }
  .contact {
    position: absolute; left: 153px; top: 752px;
    transform: rotate(-3deg); transform-origin: left top;
  }
  .contact__tab {
    position: absolute; left: 80px; top: 0;
    background: var(--white); color: var(--purple);
    font-family: "Oswald", sans-serif; font-weight: 600;
    font-size: 28px; line-height: 1; padding: 10px 22px 8px;
    border-radius: 4px 4px 0 0;
  }
  .contact__phone {
    position: absolute; left: 0; top: 44px; width: 496px; height: 120px;
    background: var(--purple); border: 3px solid var(--white); border-radius: 6px;
    display: flex; align-items: center; justify-content: center;
    font-weight: 800; font-size: 72px; letter-spacing: -3px;
  }
  .footer-band {
    position: absolute; left: 33px; top: 937px; width: 1096px; height: 60px;
    background: var(--white);
  }
  .website {
    position: absolute; left: 161px; top: 952px;
    display: flex; align-items: center; gap: 10px;
    color: var(--purple); font-weight: 700; font-style: italic; font-size: 25px;
  }
  .brand-block {
    position: absolute; left: 765px; top: 853px; width: 266px; height: 148px;
    background: var(--navy-deep);
    display: flex; flex-direction: column; align-items: center; justify-content: center; gap: 10px;
  }
  .brand-block__mark { width: 16px; height: 16px; background: var(--white); }
  .brand-block__name {
    font-weight: 600; font-size: 20px; line-height: 1.2; text-align: center; letter-spacing: 1px;
    color: var(--white);
  }
</style>
</head>
<body>
<main class="flyer">
  <div class="flyer__photo" role="img" aria-label="Smiling maintenance technician in a blue uniform giving a thumbs up in a modern kitchen"></div>
  <div class="flyer__frame"></div>

  <div class="headline headline__script">Join our</div>
  <h1 class="headline headline__main">TEAM</h1>

  <ul class="perks">
    <li style="top:326px">95% approval rating on all submitted estimates.</li>
    <li style="top:426px">Guaranteed work volume.</li>
    <li style="top:492px;width:480px">Material purchasing program to help vendors with low capital or no or bad credit.</li>
    <li style="top:626px">Weekly secure direct deposit with net 30 payment terms.</li>
  </ul>

  <div class="divider"></div>

  <section class="requirements">
    <h2 class="requirements__title">REQUIREMENTS TO BECOME A<br>VENDOR</h2>
    <ul class="requirements__list">
      <li style="top:404px">Auto insurance</li>
      <li style="top:457px">Certificate of general liability insurance</li>
      <li style="top:509px">Workman’s Compensation or state issued exemption letter</li>
      <li style="top:592px">Drive License or state issued ID card</li>
      <li style="top:645px">Coverage area</li>
      <li style="top:698px">Any speciality Licenses</li>
    </ul>
  </section>

  <div class="contact">
    <div class="contact__tab">CONTACT</div>
    <div class="contact__phone">731-555-0148</div>
  </div>

  <div class="footer-band"></div>
  <div class="website">
    <svg width="28" height="28" viewBox="0 0 28 28" fill="none" stroke="#6a2a93" stroke-width="2">
      <circle cx="14" cy="14" r="12"/>
      <ellipse cx="14" cy="14" rx="5.5" ry="12"/>
      <line x1="2" y1="14" x2="26" y2="14"/>
    </svg>
    <span>www.brindleassetmanagement.com</span>
  </div>

  <div class="brand-block">
    <span class="brand-block__mark"></span>
    <span class="brand-block__name">BRINDLE<br>ASSET MANAGEMENT</span>
  </div>
</main>
</body>
</html>
```